Powerpoint, Graphics for Sermon Series

I am starting a sermon series on the short letters if Scripture that are between Hebrews and Revelation. The sermon series will be called "Walking Unmarked Trails: Lasting Lessons from Quiet Hills."

Think about finding a packet of letters in an Attic. There is only the dialogue of the writer. We don't know exactly what the receivers were going through or even what their response to the letters were/are!

Target Market(s)

Local Church

Industry/Entity Type

Christian

Font styles to use
Serif
Sans Serif

Colors

Designer to choose colors to be used in the design.

Requirements
Must have
• Powerpoint Slide with Title -
• Background Slide -
• It would be great to have both JPG, PNG, and Photoshop/Indesign that can be used for powerpoint, both in 4x3 ration and wide... Need Title Slide with typography and background slide for text to go over the top of.
• Stick with the theme -- Walking Unmarked Trails
• I am including our church logo, but don't feel like you need to use it in anyway.
Nice to have
• Social Media Slides - Square Slide, Facebook Header
• Greyscale Version?

```html
<!DOCTYPE html>
<html lang="en">
<head>
<meta charset="utf-8">
<title>Walking Unmarked Trails – Content Slide</title>
<link rel="stylesheet" href="https://fonts.googleapis.com/css2?family=Arvo:wght@700&family=Open+Sans:wght@400;600&display=swap">
<style>
  :root {
    --brown: #5a3a22;
    --orange: #f29a12;
    --subtitle: #c8780a;
    --text: #3a2f28;
    --paper: #f7f4f1;
    --paper-shade: #ece6e0;
    --white: #ffffff;
  }
  * { margin: 0; padding: 0; box-sizing: border-box; }
  html, body { width: 1200px; height: 900px; overflow: hidden; background: var(--white); }
  .slide {
    position: relative;
    width: 1200px;
    height: 900px;
    overflow: hidden;
    background: radial-gradient(ellipse at 30% 60%, var(--white) 0%, var(--paper) 55%, var(--paper-shade) 100%);
    font-family: "Open Sans", Arial, sans-serif;
  }
  .side-art { position: absolute; inset: 0; width: 1200px; height: 900px; }
  .slide-title {
    position: absolute;
    left: 48px;
    top: 28px;
    font-family: "Arvo", Georgia, serif;
    font-weight: 700;
    font-size: 54px;
    line-height: 1.2;
    color: var(--brown);
    white-space: nowrap;
  }
  .title-rule {
    position: absolute;
    left: 0;
    top: 98px;
    width: 790px;
    height: 3px;
    background: var(--orange);
  }
  .content {
    position: absolute;
    left: 50px;
    top: 160px;
    width: 570px;
  }
  .subtitle {
    font-weight: 600;
    font-size: 32px;
    color: var(--subtitle);
    line-height: 1.2;
    margin-bottom: 6px;
    white-space: nowrap;
  }
  .body-copy {
    font-size: 20.5px;
    line-height: 39px;
    color: var(--text);
  }
  .photo {
    position: absolute;
    left: 642px;
    width: 386px;
    height: 278px;
    background: linear-gradient(180deg, #cfe0f0 0%, #e8eef2 30%, #9b5a3c 48%, #8a4a32 70%, #6f9a3e 84%, #5d8a34 100%);
  }
  .photo--top { top: 172px; }
  .photo--bottom { top: 483px; }
  .church-name {
    position: absolute;
    left: 18px;
    bottom: 22px;
    display: flex;
    align-items: center;
    gap: 10px;
    font-weight: 600;
    font-size: 24px;
    color: var(--brown);
  }
  .church-name .mark {
    width: 16px;
    height: 16px;
    background: var(--brown);
  }
</style>
</head>
<body>
<main class="slide">
  <svg class="side-art" viewBox="0 0 1200 900">
    <defs>
      <linearGradient id="bibleTone" x1="0" y1="0" x2="1" y2="1">
        <stop offset="0" stop-color="#f0a43a"/>
        <stop offset="0.5" stop-color="#d97f14"/>
        <stop offset="1" stop-color="#a85808"/>
      </linearGradient>
    </defs>
    <path class="accent-band" d="M845 0 Q1200 450 870 900 L1200 900 L1200 0 Z" fill="var(--orange)"/>
    <path class="bible-photo" role="img" aria-label="Close-up of an open Bible resting on a wooden pew"
          d="M930 0 Q1170 450 950 900 L1200 900 L1200 0 Z" fill="url(#bibleTone)"
          stroke="var(--white)" stroke-width="9"/>
  </svg>

  <h1 class="slide-title">Walking Unmarked Trails</h1>
  <div class="title-rule"></div>

  <section class="content">
    <h2 class="subtitle">Lasting Lessons from Quiet Hills</h2>
    <p class="body-copy">Imagine climbing into a quiet attic and finding a packet of old letters tied with string. We hear only one voice, the writer's. We do not know what the readers were facing, or how they answered once the pages were read. The short letters between Hebrews and Revelation are like that: James, Peter, John and Jude write to scattered churches walking paths no one had marked for them. They wrote to people tired of waiting, tempted to drift and unsure whom to trust. Their words still reach us, pointing to a faith that works, a hope that lives and a love practiced in truth. As we walk these unmarked trails together, we will listen closely and find lasting lessons for our own steps.</p>
  </section>

  <div class="photo photo--top" role="img" aria-label="Red brick church with white steeple under a summer sky"></div>
  <div class="photo photo--bottom" role="img" aria-label="Red brick church with white steeple under a summer sky"></div>

  <div class="church-name"><span class="mark"></span>Cedar Hollow Church</div>
</main>
</body>
</html>
```